Modern Label for cleaning products for the brand Vorlix

We need a label design for our line of cleaning products. The label should feature our logo and an image to identify the product's intended use. I've added our logo and an image for use. This only concerns the design of the label on the front of the bottle.

Label dimensions:
Label 1 (500ml bottle with spray): width 58mm x height 115mm
Label 2: (1L bottle): width 73mm x height 140mm
The design must be consistent for both bottles which you find in the pictures.

The bottles to be labeled are white. See the attachment for a photo of the bottles.

The photo must also appear on the label to identify the product's intended use.

Product information:
Brand: Vorlix
Product: Sanitary Cleaner

This text must be placed on the label:
"Cleans, descales & freshens. followed with this text: "Ideal for quick and powerful cleaning. A ready-to-use product for everyday use."

- Mention the seperate USP's: Sanitary, Bathroom, Toilet, Wet areas

Appearance: This is a consumer product, but it must have a professional appearance. We would like to see a design that use the color blue from our logo.

Target Market(s)

Consumers who take care of their homes and want to maintain it the correct (professional) way

Font styles to use
Sans Serif

Colors
0054AA
0677BA
7BADD7
CADEEF
E8F1F8

Requirements
Must have
• USP's + use of image and logo + blend in 1 design
Nice to have
• Keep the color of the logo in the design
Should not have
• Comic sans

```html
<!DOCTYPE html>
<html lang="en">
<head>
<meta charset="utf-8">
<title>Vorlix Sanitary Cleaner – Label Set</title>
<link href="https://fonts.googleapis.com/css2?family=Montserrat:wght@400;500;700;800&family=Arimo:wght@400&display=swap" rel="stylesheet">
<style>
  :root{
    --bg-center:#fbfcf0;
    --bg-edge:#dde78f;
    --brand-blue:#0a8ad0;
    --deep-blue:#0677ba;
    --sky:#5ab1e0;
    --light-sky:#7bc2e8;
    --pale-sky:#a9d9f1;
    --ice:#e8f1f8;
    --ink:#1d1d1b;
    --white:#ffffff;
    --dim-line:#2f6fa8;
    --photo-light:#e9ecee;
    --photo-mid:#b9bbbd;
    --photo-dark:#8d8e8f;
  }
  html,body{margin:0;padding:0;width:1200px;height:1200px;overflow:hidden;}
  body{background:radial-gradient(circle at 50% 50%,var(--bg-center) 0%,var(--bg-edge) 100%);}
  .board{display:block;width:1200px;height:1200px;}
  .brand-name{font-family:"Montserrat",sans-serif;font-weight:700;fill:var(--ink);}
  .title-main{font-family:"Montserrat",sans-serif;font-weight:800;fill:var(--white);}
  .title-sub{font-family:"Montserrat",sans-serif;font-weight:500;fill:var(--brand-blue);}
  .usp{font-family:"Montserrat",sans-serif;font-weight:800;fill:var(--white);}
  .tagline{font-family:"Montserrat",sans-serif;font-weight:700;fill:var(--white);}
  .use-areas{font-family:"Montserrat",sans-serif;font-weight:700;fill:var(--ice);letter-spacing:0.5px;}
  .body-copy{font-family:"Montserrat",sans-serif;font-weight:400;fill:var(--white);}
  .volume{font-family:"Montserrat",sans-serif;font-weight:700;fill:var(--white);}
  .dim-text{font-family:"Arimo",sans-serif;font-weight:400;fill:var(--dim-line);}
  .dim-line{stroke:var(--dim-line);stroke-width:2;fill:none;}
  .dim-arrow{fill:var(--dim-line);}
  .label-base{fill:var(--brand-blue);}
  .band-light{stroke:var(--light-sky);fill:none;}
  .band-pale{stroke:var(--pale-sky);fill:none;}
  .band-sky{stroke:var(--sky);fill:none;}
  .check{stroke:var(--white);fill:none;stroke-width:3;stroke-linecap:round;stroke-linejoin:round;}
  .brand-dot{fill:var(--white);}
  .brand-dot-hero{fill:var(--brand-blue);}
  .seal-outer{fill:var(--white);}
  .seal-inner{fill:var(--brand-blue);}
</style>
</head>
<body>
<svg class="board" viewBox="0 0 1920 1920" xmlns="http://www.w3.org/2000/svg">
  <defs>
    <linearGradient id="photoTone" x1="0" y1="0" x2="0" y2="1">
      <stop offset="0" stop-color="var(--photo-light)"/>
      <stop offset="0.55" stop-color="var(--photo-mid)"/>
      <stop offset="1" stop-color="var(--photo-dark)"/>
    </linearGradient>
    <radialGradient id="cornerGlow" cx="1" cy="0" r="1">
      <stop offset="0" stop-color="var(--light-sky)" stop-opacity="0.75"/>
      <stop offset="1" stop-color="var(--light-sky)" stop-opacity="0"/>
    </radialGradient>
    <clipPath id="clipSmall"><rect x="309" y="797" width="486" height="964"/></clipPath>
    <clipPath id="clipLarge"><rect x="1082" y="587" width="612" height="1174"/></clipPath>
  </defs>

  <g class="brand-block">
    <circle class="brand-dot-hero" cx="550" cy="303" r="80"/>
    <text class="brand-name" x="550" y="450" font-size="92" text-anchor="middle">vorlix</text>
  </g>

  <g class="dimensions">
    <line class="dim-line" x1="309" y1="730" x2="309" y2="778"/>
    <line class="dim-line" x1="795" y1="730" x2="795" y2="778"/>
    <line class="dim-line" x1="315" y1="751" x2="420" y2="751"/>
    <line class="dim-line" x1="688" y1="751" x2="789" y2="751"/>
    <path class="dim-arrow" d="M311 751 L343 742 L343 760 Z"/>
    <path class="dim-arrow" d="M793 751 L761 742 L761 760 Z"/>
    <text class="dim-text" x="555" y="770" font-size="52" text-anchor="middle">58.00 mm</text>

    <line class="dim-line" x1="236" y1="797" x2="300" y2="797"/>
    <line class="dim-line" x1="236" y1="1761" x2="300" y2="1761"/>
    <line class="dim-line" x1="257" y1="803" x2="257" y2="1125"/>
    <line class="dim-line" x1="257" y1="1415" x2="257" y2="1755"/>
    <path class="dim-arrow" d="M257 799 L248 831 L266 831 Z"/>
    <path class="dim-arrow" d="M257 1759 L248 1727 L266 1727 Z"/>
    <text class="dim-text" font-size="52" text-anchor="middle" transform="translate(276 1272) rotate(-90)">115.00 mm</text>

    <line class="dim-line" x1="1082" y1="520" x2="1082" y2="568"/>
    <line class="dim-line" x1="1694" y1="520" x2="1694" y2="568"/>
    <line class="dim-line" x1="1088" y1="541" x2="1258" y2="541"/>
    <line class="dim-line" x1="1522" y1="541" x2="1688" y2="541"/>
    <path class="dim-arrow" d="M1084 541 L1116 532 L1116 550 Z"/>
    <path class="dim-arrow" d="M1692 541 L1660 532 L1660 550 Z"/>
    <text class="dim-text" x="1390" y="560" font-size="52" text-anchor="middle">73.00 mm</text>

    <line class="dim-line" x1="998" y1="587" x2="1062" y2="587"/>
    <line class="dim-line" x1="998" y1="1761" x2="1062" y2="1761"/>
    <line class="dim-line" x1="1019" y1="593" x2="1019" y2="1025"/>
    <line class="dim-line" x1="1019" y1="1315" x2="1019" y2="1755"/>
    <path class="dim-arrow" d="M1019 589 L1010 621 L1028 621 Z"/>
    <path class="dim-arrow" d="M1019 1759 L1010 1727 L1028 1727 Z"/>
    <text class="dim-text" font-size="52" text-anchor="middle" transform="translate(1038 1170) rotate(-90)">140.00 mm</text>
  </g>

  <!-- Label 500 ml -->
  <g class="label label-500" clip-path="url(#clipSmall)">
    <rect class="label-base" x="309" y="797" width="486" height="964"/>
    <rect x="560" y="797" width="235" height="200" fill="url(#cornerGlow)"/>
    <g role="img" aria-label="Photo of a bright modern bathroom with bathtub, washbasin and glass shower">
      <path d="M362 1043 H795 V1405 C610 1405 400 1330 362 1043 Z" fill="url(#photoTone)"/>
    </g>
    <path class="band-light" stroke-width="26" d="M334 780 C318 1120 420 1400 820 1452"/>
    <path class="band-pale" stroke-width="14" d="M366 780 C350 1110 450 1380 820 1420"/>
    <path class="band-sky" stroke-width="44" d="M300 1180 C360 1420 560 1500 820 1500"/>
    <path class="band-pale" stroke-width="16" d="M320 1260 C420 1450 600 1535 820 1538"/>

    <circle class="brand-dot" cx="551" cy="873" r="38"/>
    <text class="brand-name" x="552" y="943" font-size="36" text-anchor="middle">vorlix</text>
    <text class="title-main" x="552" y="1030" font-size="64" text-anchor="middle">SANITARY</text>
    <text class="title-sub" x="552" y="1086" font-size="54" text-anchor="middle">CLEANER</text>

    <circle class="seal-outer" cx="651" cy="1443" r="86"/>
    <circle class="seal-inner" cx="651" cy="1443" r="56"/>

    <g class="usp-list">
      <circle class="check" cx="343" cy="1460" r="11"/><path class="check" d="M337 1460 l5 5 l10 -12"/>
      <text class="usp" x="368" y="1472" font-size="34">Cleans</text>
      <circle class="check" cx="343" cy="1494" r="11"/><path class="check" d="M337 1494 l5 5 l10 -12"/>
      <text class="usp" x="368" y="1506" font-size="34">Descales</text>
      <circle class="check" cx="343" cy="1528" r="11"/><path class="check" d="M337 1528 l5 5 l10 -12"/>
      <text class="usp" x="368" y="1540" font-size="34">Freshens</text>
    </g>
    <text class="tagline" x="329" y="1575" font-size="19">Ideal for quick and powerful cleaning.</text>
    <text class="tagline" x="329" y="1601" font-size="19">A ready-to-use product for everyday use</text>
    <text class="use-areas" x="552" y="1632" font-size="16" text-anchor="middle">Sanitary · Bathroom · Toilet · Wet areas</text>
    <text class="body-copy" x="552" y="1664" font-size="16.5" text-anchor="middle">We use 100% certified organic cleaners,</text>
    <text class="body-copy" x="552" y="1685" font-size="16.5" text-anchor="middle">ensuring a safe working environment free</text>
    <text class="body-copy" x="552" y="1706" font-size="16.5" text-anchor="middle">of harmful chemicals.</text>
    <text class="volume" x="552" y="1745" font-size="26" text-anchor="middle">500ml</text>
  </g>

  <!-- Label 1 L -->
  <g class="label label-1000" clip-path="url(#clipLarge)">
    <rect class="label-base" x="1082" y="587" width="612" height="1174"/>
    <rect x="1400" y="587" width="294" height="240" fill="url(#cornerGlow)"/>
    <g role="img" aria-label="Photo of a bright modern bathroom with bathtub, washbasin and glass shower">
      <path d="M1148 877 H1694 V1378 C1460 1378 1200 1290 1148 877 Z" fill="url(#photoTone)"/>
    </g>
    <path class="band-light" stroke-width="32" d="M1113 570 C1092 990 1220 1335 1720 1400"/>
    <path class="band-pale" stroke-width="18" d="M1153 570 C1132 980 1250 1310 1720 1360"/>
    <path class="band-sky" stroke-width="56" d="M1070 1090 C1150 1380 1400 1480 1720 1480"/>
    <path class="band-pale" stroke-width="20" d="M1095 1190 C1220 1420 1440 1525 1720 1528"/>

    <circle class="brand-dot" cx="1388" cy="663" r="50"/>
    <text class="brand-name" x="1389" y="752" font-size="46" text-anchor="middle">vorlix</text>
    <text class="title-main" x="1388" y="860" font-size="84" text-anchor="middle">SANITARY</text>
    <text class="title-sub" x="1388" y="932" font-size="68" text-anchor="middle">CLEANER</text>

    <circle class="seal-outer" cx="1512" cy="1382" r="108"/>
    <circle class="seal-inner" cx="1512" cy="1382" r="71"/>

    <g class="usp-list">
      <circle class="check" cx="1125" cy="1402" r="14"/><path class="check" d="M1118 1402 l6 6 l12 -15"/>
      <text class="usp" x="1157" y="1416" font-size="43">Cleans</text>
      <circle class="check" cx="1125" cy="1445" r="14"/><path class="check" d="M1118 1445 l6 6 l12 -15"/>
      <text class="usp" x="1157" y="1459" font-size="43">Descales</text>
      <circle class="check" cx="1125" cy="1488" r="14"/><path class="check" d="M1118 1488 l6 6 l12 -15"/>
      <text class="usp" x="1157" y="1502" font-size="43">Freshens</text>
    </g>
    <text class="tagline" x="1108" y="1547" font-size="24">Ideal for quick and powerful cleaning.</text>
    <text class="tagline" x="1108" y="1580" font-size="24">A ready-to-use product for everyday use</text>
    <text class="use-areas" x="1389" y="1616" font-size="20" text-anchor="middle">Sanitary · Bathroom · Toilet · Wet areas</text>
    <text class="body-copy" x="1389" y="1652" font-size="21" text-anchor="middle">We use 100% certified organic cleaners,</text>
    <text class="body-copy" x="1389" y="1677" font-size="21" text-anchor="middle">ensuring a safe working environment free</text>
    <text class="body-copy" x="1389" y="1702" font-size="21" text-anchor="middle">of harmful chemicals.</text>
    <text class="volume" x="1389" y="1744" font-size="34" text-anchor="middle">1.000ml</text>
  </g>
</svg>
</body>
</html>
```